Quorva - corporate Business Card

We need a good look and innovative business card for a new start up company based in Los Angeles called "Quorva". We are in a payment business, including payment card, app, and ewallet. We are expert in online payment and Card not present (CNP) transaction.
We need an innovative, modern business card.

Our logo font is Aero Matics

Target Market(s)

Startup - Bank - Online Payment - Card Manufacturing

Industry/Entity Type

Startup

Contact Information for Business Card

phone: 555 014 7396 - Address: 4172 Marlowe blvd, Varden City, CA 90299

Requirements
Must have
• Message: innovative, professional, expert, high tech, trust, online payment expert, security
Nice to have
• no comment
Should not have
• no Comment

```html
<!DOCTYPE html>
<html lang="en">
<head>
<meta charset="utf-8">
<title>Quorva – Business Card</title>
<link rel="stylesheet" href="https://fonts.googleapis.com/css2?family=Arimo:wght@400;700&display=swap">
<style>
  :root {
    --stage: #2e2e2e;
    --paper: #ffffff;
    --paper-shade: #ececec;
    --brand-red: #c0202e;
    --brand-red-deep: #8e1620;
    --ink: #3a3a3a;
    --ink-soft: #555555;
    --band-grey: #6f6f6f;
    --white: #ffffff;
  }
  * { box-sizing: border-box; margin: 0; padding: 0; }
  html, body {
    width: 1200px; height: 997px; overflow: hidden;
    background: var(--stage);
    font-family: "Arimo", Arial, sans-serif;
  }
  .canvas { position: relative; width: 1200px; height: 997px; }

  .card {
    position: absolute;
    width: 665px; height: 380px;
    border-radius: 18px;
    overflow: hidden;
    box-shadow: 0 14px 40px rgba(0,0,0,.45);
  }

  /* Front side */
  .card-front {
    left: 120px; top: 80px;
    background: linear-gradient(160deg, var(--paper) 0%, var(--paper) 55%, var(--paper-shade) 100%);
  }
  .front-brand {
    position: absolute; right: 40px; top: 34px;
    display: flex; align-items: center; gap: 14px;
  }
  .brand-dot {
    width: 58px; height: 58px; border-radius: 50%;
    background: var(--brand-red);
  }
  .front-brand .brand-name {
    font-weight: 700; font-size: 50px; color: var(--brand-red);
    letter-spacing: 1px; line-height: 1;
  }
  .rule {
    position: absolute; left: 40px; right: 30px; top: 180px;
    height: 1px; background: var(--brand-red);
  }
  .holder { position: absolute; left: 40px; top: 154px; }
  .holder-name {
    font-weight: 700; font-size: 18px; color: var(--brand-red);
    letter-spacing: .5px;
  }
  .holder-role {
    position: absolute; top: 31px; left: 0;
    font-size: 15px; color: var(--ink); white-space: nowrap;
  }
  .company {
    position: absolute; right: 36px; top: 212px;
    text-align: right; line-height: 1.3;
  }
  .company-name { font-weight: 700; font-size: 16px; color: var(--brand-red); }
  .company-address { font-size: 14px; color: var(--ink); }
  .contacts {
    position: absolute; left: 40px; top: 262px;
    list-style: none; font-size: 16px; color: var(--ink-soft);
  }
  .contacts li { display: flex; align-items: center; gap: 10px; height: 28px; }
  .contact-icon { width: 18px; height: 18px; flex: none; }
  .front-bands { position: absolute; left: 0; bottom: 0; width: 665px; height: 80px; }
  .web {
    position: absolute; right: 36px; bottom: 42px;
    font-size: 13px; font-weight: 700; color: var(--white);
    letter-spacing: 4px;
  }

  /* Back side */
  .card-back {
    left: 415px; top: 530px;
    background: linear-gradient(135deg, var(--brand-red) 0%, var(--brand-red-deep) 100%);
    display: flex; flex-direction: column; align-items: center; justify-content: center;
    gap: 22px;
  }
  .back-dot {
    width: 150px; height: 150px; border-radius: 50%;
    background: var(--white);
  }
  .card-back .brand-name {
    font-weight: 700; font-size: 72px; color: var(--white);
    letter-spacing: 2px; line-height: 1;
  }
</style>
</head>
<body>
<main class="canvas">

  <section class="card card-front" aria-label="Business card front">
    <div class="front-brand">
      <span class="brand-dot"></span>
      <span class="brand-name">quorva</span>
    </div>

    <div class="holder">
      <p class="holder-name">DORANA VELL</p>
      <p class="holder-role">Attorney</p>
    </div>
    <div class="rule"></div>

    <div class="company">
      <p class="company-name">QUORVA PVT LTD</p>
      <p class="company-address">4172 Marlowe blvd, Varden City,<br>CA 90299</p>
    </div>

    <ul class="contacts">
      <li>
        <svg class="contact-icon" viewBox="0 0 18 18" aria-hidden="true">
          <circle cx="9" cy="9" r="9" fill="var(--brand-red)"/>
          <path d="M6 5.2c.4-.3.9-.2 1.1.2l.8 1.4c.2.4.1.8-.2 1l-.5.4c.4.9 1.1 1.6 2 2l.4-.5c.3-.3.7-.4 1-.2l1.4.8c.4.2.5.7.2 1.1l-.6.7c-.4.4-1 .5-1.6.3C8 11.6 6.4 10 5.6 8c-.2-.6-.1-1.2.3-1.6z" fill="var(--white)"/>
        </svg>
        555 014 7396
      </li>
      <li>
        <svg class="contact-icon" viewBox="0 0 18 18" aria-hidden="true">
          <circle cx="9" cy="9" r="9" fill="var(--brand-red)"/>
          <rect x="4.5" y="6" width="9" height="6.2" rx="1" fill="var(--white)"/>
          <path d="M4.8 6.3 9 9.4l4.2-3.1" fill="none" stroke="var(--brand-red)" stroke-width="1"/>
        </svg>
        dvell@quorva.com
      </li>
    </ul>

    <svg class="front-bands" viewBox="0 0 665 80" preserveAspectRatio="none" aria-hidden="true">
      <path d="M0 64 H300 C318 64 322 52 330 38 C336 28 342 24 356 24 H665 V54 H362 C350 54 346 58 342 66 C336 76 328 80 312 80 H0 Z" fill="var(--band-grey)"/>
      <path d="M330 22 C338 8 346 4 360 4 H665 V44 H364 C352 44 348 48 344 56 L340 62 H318 C324 54 326 34 330 22 Z" fill="var(--brand-red)"/>
    </svg>
    <p class="web">www.quorva.com</p>
  </section>

  <section class="card card-back" aria-label="Business card back">
    <span class="back-dot"></span>
    <span class="brand-name">quorva</span>
  </section>

</main>
</body>
</html>
```